Hardcore nerd needs to stand out in a sea of dull Defence business cards

Wombarra Devices is a new Australian consulting engineering company that turns research and theory into practical systems. No evangelistic fluff, just mathematics and physics into electronic and optical circuits for consumer products, scientific research or Defence applications.

We already have a recognised logo (provided) which is often dark blue/black on a light background but we're open to other combinations. (Us engineers tend to have limited aesthetic imagination :)

Some of our recent products have included:
* Instrumentation for electrical testing,
* Radar jammers,
* GPS antenna design,
* Satellite tracking systems,
* High power lasers

We're open to both single and double-sided designs - happy to be convinced either way.

P.S. Another group is working on the web page, so - alas - our web site is currently of no use for images/ideas...

Target Market(s)

Engineering managers,
Scientists

Contact Information for Business Card

Dr Colin Harte
R&D Engineer

colin@wombarradevices.com.au
0427 563 710

PO Box XXX (to be confirmed)
Kelsby ACT 2917
Australia

Font styles to use
Serif
Sans Serif

Colors

Designer to choose colors to be used in the design.

Requirements
Must have
• My contact details!
• I've had many (great) "bold and plain" designs submitted already, so feel free to be artistically creative :)
• Happy to take advice re fonts/colours/printability etc.
Nice to have
• I'm not sure if "lists" are more at home on a CV than a business card, but representative services include:
• Applied electromagnetics
• RF and high speed electronics
• Signal and image processing
• Electro-optical and laser systems
• Concept-to-prototype design services
• If you're considering double sided cards, then often measuring/alignment grids/rulers feature on the back of similar cards.
• e.g. https://www.veltranoptics.example/newgrouppage9.cfm?objectgroup_id=4183
• https://www.veltranoptics.example/newgrouppage9.cfm?objectgroup_ID=4185
• ..or even a "Smith chart" (google will return lots)
• Generic images to represent a capability might work - googling images associated with keyword for each of these areas might help:
• - "passive radar", "phased array", "fdtd", "vircator"
• RF and high speed electronic design
• - "smith chart", "microstrip circuits", "dimensioned drawing", "electronic schematic"
• - "dft", "iir filter"
• - "optical cavity". "laser energy level diagram"
• Background/watermarked images outlines/wireframes/schematics would probably look OK.
Should not have
• If a list of projects/services is provided, it is important not to make the client feel that this is "all" the company can do. Engineering design is a creative discipline (like graphics :)
• Please, no stock "military" snaps like planes, missiles, etc!

```html
<!DOCTYPE html>
<html lang="en">
<head>
<meta charset="utf-8">
<title>Wombarra Devices – Business Card</title>
<link rel="stylesheet" href="https://fonts.googleapis.com/css2?family=Lato:wght@400;700;900&display=swap">
<style>
  :root {
    --backdrop-light: #4a4a4a;
    --backdrop-dark: #1e1e1e;
    --navy: #1f2a6b;
    --navy-deep: #1b255e;
    --navy-soft: #2a3880;
    --paper: #ffffff;
    --ink-grey: #6b6b6b;
  }
  * { box-sizing: border-box; margin: 0; padding: 0; }
  html, body { width: 1200px; height: 675px; overflow: hidden; }
  body {
    background: radial-gradient(ellipse at 50% 40%, var(--backdrop-light), var(--backdrop-dark) 75%);
    font-family: "Lato", sans-serif;
    position: relative;
  }
  .card {
    position: absolute;
    top: 195px;
    width: 500px;
    height: 286px;
    border-radius: 2px;
    box-shadow: 0 12px 30px rgba(0,0,0,.55);
    overflow: hidden;
  }
  /* Front: navy, blind-embossed wordmark */
  .card-front {
    left: 70px;
    background: linear-gradient(135deg, var(--navy-deep) 0%, var(--navy-soft) 45%, var(--navy-deep) 100%);
  }
  .emboss-mark {
    position: absolute;
    left: 58px; top: 78px;
    width: 130px; height: 130px;
    border-radius: 50%;
    border: 16px solid rgba(255,255,255,.05);
    box-shadow: inset 1px 1px 2px rgba(0,0,0,.35), 1px 1px 1px rgba(255,255,255,.06);
  }
  .emboss-name {
    position: absolute;
    left: 210px; top: 118px;
    font-weight: 900;
    font-size: 34px;
    letter-spacing: 1px;
    line-height: 1;
    color: var(--navy-deep);
    text-transform: uppercase;
    text-shadow: -1px -1px 0 rgba(0,0,0,.35), 1px 1px 0 rgba(255,255,255,.08);
  }
  /* Back: white with details */
  .card-back {
    left: 630px;
    background: var(--paper);
  }
  .brand {
    position: absolute;
    left: 30px; top: 122px;
    display: flex;
    align-items: center;
    gap: 10px;
  }
  .brand-dot {
    width: 40px; height: 40px;
    border-radius: 50%;
    background: var(--navy);
    flex: none;
  }
  .brand-name {
    font-weight: 900;
    font-size: 17px;
    line-height: 1.05;
    color: var(--navy);
    text-transform: uppercase;
    letter-spacing: .5px;
  }
  .divider {
    position: absolute;
    left: 232px; top: 64px;
    width: 1px; height: 160px;
    background: var(--navy);
  }
  .details {
    position: absolute;
    left: 250px; top: 70px;
    color: var(--ink-grey);
    font-size: 11px;
    line-height: 1.45;
  }
  .person-name {
    font-size: 18px;
    font-weight: 700;
    color: var(--navy);
    line-height: 1.1;
  }
  .person-role { margin-bottom: 10px; }
  .address { margin-bottom: 10px; }
  .contact-line { display: flex; align-items: center; gap: 5px; }
  .contact-line svg { width: 10px; height: 10px; fill: var(--navy); flex: none; }
</style>
</head>
<body>
  <section class="card card-front" aria-label="Card front">
    <div class="emboss-mark"></div>
    <div class="emboss-name">Wombarra<br>Devices</div>
  </section>

  <section class="card card-back" aria-label="Card back">
    <div class="brand">
      <div class="brand-dot"></div>
      <div class="brand-name">Wombarra<br>Devices</div>
    </div>
    <div class="divider"></div>
    <div class="details">
      <div class="person-name">Dr Colin Harte</div>
      <div class="person-role">R&amp;D Engineer</div>
      <div class="address">PO Box XXX (to be confirmed)<br>Kelsby ACT 2917, Australia</div>
      <div class="contact-line">
        <svg viewBox="0 0 10 10"><path d="M2 0.5 L3.6 2.6 L2.7 3.6 Q3.6 5.6 6.4 7.3 L7.4 6.4 L9.5 8 L8.3 9.5 Q3.5 9 0.5 1.7 Z"/></svg>
        <span>0427 563 710</span>
      </div>
      <div class="contact-line">
        <svg viewBox="0 0 10 10"><path d="M0.5 2 H9.5 V8 H0.5 Z M1 2.5 L5 5.5 L9 2.5" stroke="#fff" stroke-width=".7"/></svg>
        <span>colin@wombarradevices.com.au</span>
      </div>
      <div class="contact-line">
        <svg viewBox="0 0 10 10"><circle cx="5" cy="5" r="4.5"/><path d="M0.5 5 H9.5 M5 0.5 Q2.5 5 5 9.5 M5 0.5 Q7.5 5 5 9.5" stroke="#fff" stroke-width=".6" fill="none"/></svg>
        <span>wombarradevices.com.au</span>
      </div>
    </div>
  </section>
</body>
</html>
```